Harbourline Electrical Solutions

On one side. LOGO (underneath:) Commercial Industrial Residential

- NAME & CONTACT DETAILS

Marcus T. Hollings
Project Manager

(Cell icon) (441) 555-0187
(Email icon) hlelectricalsolutions@mailvento.com
(Facebook & Instagram icons )@hlelectricalsolutions

Other side: LOGO - underneath ELECTRICAL CONSTRUCTION & MAINTENANCE . LED LIGHTING & AUTOMATION . LIFE SAFETY SYSTEMS (FIRE ALARM / SECURITY) . DATA & COMMUNICATION

```html
<!DOCTYPE html>
<html lang="en">
<head>
<meta charset="utf-8">
<title>Harbourline Electrical Solutions – Business Card</title>
<link href="https://fonts.googleapis.com/css2?family=Montserrat:wght@300;400;500;600;700&display=swap" rel="stylesheet">
<style>
  :root {
    --teal: #11566c;
    --ink: #2b2b2b;
    --grey: #4a4a4a;
    --paper: #ffffff;
    --backdrop: #e9eaec;
  }
  * { margin: 0; padding: 0; box-sizing: border-box; }
  html, body { width: 1200px; height: 1200px; overflow: hidden; }
  body {
    background: var(--backdrop);
    font-family: "Montserrat", sans-serif;
    position: relative;
  }
  .card {
    position: absolute;
    left: 300px;
    width: 600px;
    height: 360px;
  }
  .card--front { top: 215px; background: var(--teal); color: var(--paper); }
  .card--back { top: 625px; background: var(--paper); color: var(--ink); }

  .wordmark {
    display: flex;
    align-items: center;
    gap: 12px;
    font-weight: 600;
    text-transform: uppercase;
    letter-spacing: 0.12em;
    line-height: 1.2;
  }
  .wordmark__square { width: 14px; height: 14px; flex: none; }

  .card--front .wordmark {
    position: absolute;
    left: 0; right: 0; top: 125px;
    justify-content: center;
    font-size: 22px;
  }
  .card--front .wordmark__square { background: var(--paper); }

  .services {
    position: absolute;
    left: 0; right: 0; top: 302px;
    text-align: center;
    font-weight: 300;
    font-size: 11px;
    line-height: 16px;
    text-transform: uppercase;
  }

  .card--back .wordmark {
    position: absolute;
    left: 46px; top: 38px;
    color: var(--teal);
    font-size: 17px;
  }
  .card--back .wordmark__square { background: var(--teal); }

  .sectors {
    position: absolute;
    left: 46px; top: 113px;
    font-size: 9.5px;
    font-weight: 600;
    letter-spacing: 0.22em;
    color: var(--ink);
  }
  .sectors .divider { color: var(--teal); margin: 0 5px; letter-spacing: 0; }

  .person { position: absolute; left: 46px; top: 245px; }
  .person__name { font-size: 16px; font-weight: 700; color: var(--teal); }
  .person__role { font-size: 11px; font-weight: 500; color: var(--grey); margin-top: 1px; }
  .person__rule { width: 49px; height: 2px; background: var(--teal); margin-top: 10px; }

  .contact {
    position: absolute;
    display: flex;
    align-items: center;
    gap: 5px;
    font-size: 12.5px;
    font-weight: 400;
    color: var(--grey);
  }
  .contact svg { width: 13px; height: 13px; flex: none; }
  .contact--phone { left: 46px; top: 302px; }
  .contact--email { left: 46px; top: 321px; }
  .contact--social { right: 46px; top: 321px; }
  .social-dot {
    width: 12px; height: 12px; border-radius: 50%;
    border: 1.3px solid var(--teal);
  }
</style>
</head>
<body>

<section class="card card--front" aria-label="Card front">
  <div class="wordmark">
    <span class="wordmark__square"></span>
    <span>Harbourline<br>Electrical<br>Solutions</span>
  </div>
  <p class="services">
    Electrical construction &amp; maintenance • LED lighting &amp; automation<br>
    • Life safety systems (fire alarm / security) • Data &amp; communication
  </p>
</section>

<section class="card card--back" aria-label="Card back">
  <div class="wordmark">
    <span class="wordmark__square"></span>
    <span>Harbourline<br>Electrical<br>Solutions</span>
  </div>
  <p class="sectors">COMMERCIAL<span class="divider">|</span>INDUSTRIAL<span class="divider">|</span>RESIDENTIAL</p>

  <div class="person">
    <p class="person__name">MARCUS T. HOLLINGS</p>
    <p class="person__role">Project Manager</p>
    <div class="person__rule"></div>
  </div>

  <p class="contact contact--phone">
    <svg viewBox="0 0 16 16" aria-hidden="true"><circle cx="8" cy="8" r="7.2" fill="none" stroke="#11566c" stroke-width="1.1"/><path d="M5.4 4.3l1.2-.3.8 1.9-.8.7a5 5 0 0 0 2.8 2.8l.7-.8 1.9.8-.3 1.2c-.2.5-.8.8-1.4.6A7 7 0 0 1 4.8 5.7c-.2-.6.1-1.2.6-1.4z" fill="#11566c"/></svg>
    (441) 555-0187
  </p>
  <p class="contact contact--email">
    <svg viewBox="0 0 16 16" aria-hidden="true"><circle cx="8" cy="8" r="7.2" fill="none" stroke="#11566c" stroke-width="1.1"/><rect x="4.3" y="5.3" width="7.4" height="5.4" rx="0.6" fill="none" stroke="#11566c" stroke-width="1"/><path d="M4.5 5.6L8 8.4l3.5-2.8" fill="none" stroke="#11566c" stroke-width="1"/></svg>
    hlelectricalsolutions@mailvento.com
  </p>
  <p class="contact contact--social">
    <span class="social-dot" aria-hidden="true"></span>
    @hlelectricalsolutions
  </p>
</section>

</body>
</html>
```